Book cover

I am working with my publisher to publish my book They came up with a book cover but I don't like it. I want to see different designs. The book Title is Brightwater the subtitle Ways to Guide Teams Through Storms with Poise, Purpose & Pace by Marlene T. Ostrowski
I want to use my Brand Colors including the blue. I am uploading the covers of my other book. This is a professional leadership book. The publisher will make the cover when providing them a new design. the Brightwater one is one I played with on Canva. I would like more color and to incorporate the blue. I want a spot at the top where I can write a quote. Brightwater is one word in the text so should be the same on the cover. I want the cover to show energy movement and am open to an image too. I am attaching logos for the feel of the brand and brand rgb codes.

```html
<!DOCTYPE html>
<html lang="en">
<head>
<meta charset="utf-8">
<title>Brightwater — Book Cover</title>
<link href="https://fonts.googleapis.com/css2?family=Playfair+Display:wght@500&family=Crimson+Pro:ital,wght@0,400;1,400&family=Cinzel:wght@400&display=swap" rel="stylesheet">
<style>
  :root {
    --backdrop: #000000;
    --paper: #ffffff;
    --brand-blue: #0033a0;
    --deep-blue: #001f6b;
    --bright-blue: #1f5fd6;
    --glow-cyan: #39c2ff;
    --glow-pink: #ff4fb0;
    --glow-violet: #8a4dff;
  }
  html, body {
    margin: 0;
    padding: 0;
    width: 1200px;
    height: 1200px;
    overflow: hidden;
    background: var(--backdrop);
  }
  .cover {
    position: absolute;
    left: 231px;
    top: 46px;
    width: 741px;
    height: 1111px;
    background: var(--paper);
    overflow: hidden;
  }
  .quote-spot {
    position: absolute;
    left: 70px;
    top: 18px;
    width: 601px;
    height: 62px;
    margin: 0;
    display: flex;
    align-items: center;
    justify-content: center;
    text-align: center;
    font-family: "Crimson Pro", serif;
    font-style: italic;
    font-size: 20px;
    line-height: 24px;
    color: var(--brand-blue);
  }
  .quote-spot__source {
    font-style: normal;
    font-size: 15px;
    letter-spacing: 2px;
    text-transform: uppercase;
    color: var(--glow-violet);
    display: block;
    margin-top: 4px;
  }
  .rule {
    position: absolute;
    left: 0;
    width: 100%;
  }
  .rule--top {
    top: 96px;
    height: 13px;
    background: linear-gradient(90deg, var(--brand-blue) 0%, var(--brand-blue) 55%, var(--glow-violet) 80%, var(--glow-pink) 100%);
  }
  .rule--bottom {
    top: 570px;
    height: 14px;
    background: linear-gradient(90deg, var(--glow-pink) 0%, var(--glow-violet) 20%, var(--brand-blue) 45%, var(--brand-blue) 100%);
  }
  .title-band {
    position: absolute;
    left: 0;
    top: 120px;
    width: 100%;
    height: 443px;
    background: radial-gradient(ellipse at 70% 30%, var(--bright-blue) 0%, var(--brand-blue) 45%, var(--deep-blue) 100%);
    overflow: hidden;
  }
  .energy-flow {
    position: absolute;
    left: 0;
    top: 0;
    width: 741px;
    height: 443px;
  }
  .title {
    position: absolute;
    left: 0;
    width: 100%;
    top: 155px;
    margin: 0;
    text-align: center;
    font-family: "Playfair Display", serif;
    font-weight: 500;
    font-size: 138px;
    line-height: 1;
    color: var(--paper);
    letter-spacing: -3px;
    transform: scaleX(0.84);
  }
  .subtitle {
    position: absolute;
    left: 0;
    width: 100%;
    top: 640px;
    margin: 0;
    text-align: center;
    font-family: "Crimson Pro", serif;
    font-style: italic;
    font-size: 34px;
    line-height: 49px;
    letter-spacing: 1.5px;
    color: var(--brand-blue);
  }
  .accent-wave {
    position: absolute;
    left: 170px;
    top: 800px;
    width: 401px;
    height: 40px;
  }
  .author {
    position: absolute;
    left: 0;
    width: 100%;
    top: 1000px;
    margin: 0;
    text-align: center;
    font-family: "Cinzel", serif;
    font-size: 47px;
    line-height: 1;
    letter-spacing: 0.5px;
    color: var(--brand-blue);
  }
</style>
</head>
<body>
  <main class="cover">
    <p class="quote-spot" aria-label="Space reserved for an endorsement quote">
      <span>“Place a short endorsement quote here, one or two lines long.”<span class="quote-spot__source">Endorser Name</span></span>
    </p>
    <div class="rule rule--top"></div>
    <section class="title-band">
      <svg class="energy-flow" viewBox="0 0 741 443" aria-hidden="true">
        <defs>
          <linearGradient id="flow-cyan" x1="0" x2="1" y1="0" y2="0">
            <stop offset="0" stop-color="#39c2ff" stop-opacity="0"/>
            <stop offset="0.45" stop-color="#39c2ff" stop-opacity="0.9"/>
            <stop offset="1" stop-color="#8a4dff" stop-opacity="0"/>
          </linearGradient>
          <linearGradient id="flow-pink" x1="0" x2="1" y1="0" y2="0">
            <stop offset="0" stop-color="#ff4fb0" stop-opacity="0"/>
            <stop offset="0.5" stop-color="#ff4fb0" stop-opacity="0.85"/>
            <stop offset="1" stop-color="#8a4dff" stop-opacity="0"/>
          </linearGradient>
          <radialGradient id="flare-cyan">
            <stop offset="0" stop-color="#bfeaff" stop-opacity="1"/>
            <stop offset="0.3" stop-color="#39c2ff" stop-opacity="0.6"/>
            <stop offset="1" stop-color="#39c2ff" stop-opacity="0"/>
          </radialGradient>
          <radialGradient id="flare-pink">
            <stop offset="0" stop-color="#ffc2e4" stop-opacity="1"/>
            <stop offset="0.3" stop-color="#ff4fb0" stop-opacity="0.6"/>
            <stop offset="1" stop-color="#ff4fb0" stop-opacity="0"/>
          </radialGradient>
        </defs>
        <path d="M-20 120 C 160 40, 320 200, 500 110 S 700 60, 760 90" fill="none" stroke="url(#flow-cyan)" stroke-width="3"/>
        <path d="M-20 140 C 170 70, 330 215, 510 130 S 705 85, 760 110" fill="none" stroke="url(#flow-cyan)" stroke-width="1.5" opacity="0.7"/>
        <path d="M-20 400 C 150 330, 330 450, 520 370 S 700 330, 760 350" fill="none" stroke="url(#flow-pink)" stroke-width="4"/>
        <path d="M-20 380 C 160 315, 340 430, 530 352 S 705 315, 760 330" fill="none" stroke="url(#flow-pink)" stroke-width="1.5" opacity="0.7"/>
        <path d="M-20 420 C 180 360, 360 470, 560 395 S 720 360, 760 372" fill="none" stroke="url(#flow-cyan)" stroke-width="2" opacity="0.6"/>
        <ellipse cx="290" cy="152" rx="160" ry="9" fill="url(#flare-cyan)"/>
        <ellipse cx="205" cy="435" rx="170" ry="16" fill="url(#flare-pink)"/>
      </svg>
      <h1 class="title">Brightwater</h1>
    </section>
    <div class="rule rule--bottom"></div>
    <p class="subtitle">Ways to Guide Teams Through Storms<br>with Poise, Purpose &amp; Pace</p>
    <svg class="accent-wave" viewBox="0 0 401 40" aria-hidden="true">
      <defs>
        <linearGradient id="wave-accent" x1="0" x2="1" y1="0" y2="0">
          <stop offset="0" stop-color="#0033a0" stop-opacity="0"/>
          <stop offset="0.3" stop-color="#0033a0"/>
          <stop offset="0.7" stop-color="#8a4dff"/>
          <stop offset="1" stop-color="#ff4fb0" stop-opacity="0"/>
        </linearGradient>
      </defs>
      <path d="M0 20 C 50 5, 100 35, 150 20 S 250 5, 300 20 S 370 35, 401 20" fill="none" stroke="url(#wave-accent)" stroke-width="3"/>
    </svg>
    <p class="author">Marlene T. Ostrowski</p>
  </main>
</body>
</html>
```